Luxury Wine Label for New Startup Winery

We need a wine label for our new winery startup. We have worked with a local designer but do not feel the resulting label / logo have the elevation required to present our brand as a luxury wine. Our winery is called "Quailbrook Vineyards" and we are focused on extremely high quality hand crafted artisan and estate wines from the Pacific Northwest.
We would like to see designs that utilize a tree line, or other imagery that represents the "Quailbrook" part of our company name. Another interesting feature could be wood grain.
A logo will be required based on your design so please design with this in mind:
This logo should be consistent with the wine bottle label design, and should be representative of our high end exclusive wine while giving a sense of place (Oregon/ Pacific Northwest.)
I will supply an image of the design we received from our local designer, PLEASE NOTE: in general we do like wood grain and tree line concepts but feel the execution was poorly done.
ATTN: Logo design should be suitable for use on: Bottles (Red wine/rose/white wine), Bussiness cards, vehicle signage, business signage, etc
P.S.:
If you have a design that is not outside the box we are still interested in seeing it.
Label is for a burgundy style bottle with a label height of 3.5 - 4" and a width of 3.5-4"
any label <= 4"x4" and >=3.5"x3.5" will be acceptable:
HOWEVER Width should be greater than or equal to height due to the bottle format
Target Market(s)
Wine enthusiasts with adequate discretionary budgets to afford $100 bottles of wine.
Industry/Entity Type
Wine / Winery
Requirements
Must have
- A sense of luxury, a feel of exclusivity, and a theme consistent with our product and brand name
Nice to have
- Tree line, wood grain or other wood themes. Serif fonts
Should not have
- anything cheesy, off topic, hard to read script fonts or anything that makes the label hard to read from a few feet away or too busy

```html
<!DOCTYPE html>
<html lang="en">
<head>
<meta charset="utf-8">
<title>Quailbrook Vineyards – Pinot Noir Label</title>
<link rel="stylesheet" href="https://fonts.googleapis.com/css2?family=Krona+One&display=swap">
<style>
  :root {
    --stage: #0b0b0b;
    --ink: #0a0a0a;
    --gold-light: #f6c54a;
    --gold-mid: #e9a935;
    --gold-deep: #d98a2c;
    --vine-light: #c9b25a;
    --vine-mid: #8f8a3a;
    --vine-dark: #6b7230;
    --wood-light: #8e5426;
    --wood-dark: #5f3516;
    --silver: #ececec;
  }
  * { box-sizing: border-box; margin: 0; padding: 0; }
  html, body {
    width: 1200px;
    height: 960px;
    overflow: hidden;
    background: var(--stage);
  }
  .label {
    position: absolute;
    left: 160px;
    top: 95px;
    width: 880px;
    height: 770px;
    display: block;
  }
  .label-text {
    font-family: "Krona One", sans-serif;
    text-transform: uppercase;
  }
  .brand-primary { fill: var(--gold-mid); font-size: 58px; }
  .brand-secondary { fill: var(--silver); font-size: 24px; }
  .varietal { fill: var(--ink); font-size: 34px; }
  .mark-spot { fill: var(--gold-mid); }
  .band-ink { fill: var(--ink); }
</style>
</head>
<body>
  <svg class="label" viewBox="0 0 880 770" xmlns="http://www.w3.org/2000/svg">
    <defs>
      <radialGradient id="scene-glow" cx="50%" cy="25%" r="55%">
        <stop offset="0" stop-color="#f7cf5a"/>
        <stop offset="1" stop-color="#f7cf5a" stop-opacity="0"/>
      </radialGradient>
      <linearGradient id="scene-base" x1="0" y1="0" x2="0" y2="1">
        <stop offset="0" stop-color="var(--vine-light)"/>
        <stop offset="0.55" stop-color="var(--vine-mid)"/>
        <stop offset="1" stop-color="var(--vine-dark)"/>
      </linearGradient>
      <linearGradient id="wood" x1="0" y1="0" x2="0" y2="1">
        <stop offset="0" stop-color="var(--wood-light)"/>
        <stop offset="1" stop-color="var(--wood-dark)"/>
      </linearGradient>
      <linearGradient id="gold-band" x1="0" y1="0" x2="1" y2="0">
        <stop offset="0" stop-color="var(--gold-light)"/>
        <stop offset="0.5" stop-color="var(--gold-mid)"/>
        <stop offset="1" stop-color="var(--gold-deep)"/>
      </linearGradient>
    </defs>

    <g class="vineyard-scene" role="img" aria-label="Sunlit vineyard with grape clusters and a line of evergreen trees at golden hour">
      <rect x="0" y="0" width="880" height="408" fill="url(#scene-base)"/>
      <rect x="0" y="0" width="880" height="408" fill="url(#scene-glow)"/>
    </g>
    <rect class="band-ink" x="0" y="382" width="880" height="10"/>

    <circle class="mark-spot" cx="440" cy="250" r="112"/>

    <g class="wood-band" role="img" aria-label="Warm brown wood grain panel">
      <rect x="0" y="549" width="880" height="129" fill="url(#wood)"/>
    </g>

    <path class="band-ink" d="M0 408 H880 V549 H674 L629 598 H251 L206 549 H0 Z"/>

    <text class="label-text brand-primary" x="440" y="497" text-anchor="middle"
          textLength="687" lengthAdjust="spacingAndGlyphs">Quailbrook</text>
    <text class="label-text brand-secondary" x="440" y="564" text-anchor="middle"
          textLength="277" lengthAdjust="spacingAndGlyphs">Vineyards</text>

    <rect x="0" y="678" width="880" height="92" fill="url(#gold-band)"/>
    <text class="label-text varietal" x="440" y="750" text-anchor="middle"
          textLength="393" lengthAdjust="spacingAndGlyphs">Pinot Noir</text>
  </svg>
</body>
</html>
```